Climbing Gear Company Stationary Design

We need some new stationary to standardise our business.
We require:

Business Card
A4 Letterhead
With complements slip

Our business is a Distributor and retailer of rock climbing equipment throughout Australia.
We need to the stationary (business card in particular) to reflect this.

Target Market(s)

customers, other retail outlets, overseas manufacturers.

Industry/Entity Type

Business

Requirements
Must have
• company logo
website url- www.ridgetopgearworks.com.au
email - mark@ridgetopgearworks.com
Business Address: Unit 3, 14-16 Marlowe Street, Kellerby Bay, TAS, 2371
Phone: 0438 627 194
my Name (on Business card) - Gordon Pellimore
use of Blue colour in our logo

```html
<!DOCTYPE html>
<html lang="en">
<head>
<meta charset="utf-8">
<title>Ridgetop Gearworks – Business Card</title>
<link rel="stylesheet" href="https://fonts.googleapis.com/css2?family=Open+Sans:ital,wght@0,400;0,700;0,800;1,700&display=swap">
<style>
  :root {
    --brand-blue: #213f8a;
    --card-white: #ffffff;
    --ink-dark: #3a3a3a;
    --ink-body: #444444;
    --rule-grey: #c8c8cc;
    --swoosh-grey: #a9adb8;
    --backdrop: #ecebe8;
  }
  * { margin: 0; padding: 0; box-sizing: border-box; }
  html, body { width: 1200px; height: 440px; overflow: hidden; }
  body {
    background: var(--backdrop);
    font-family: "Open Sans", Arial, sans-serif;
    position: relative;
  }
  .card {
    position: absolute;
    width: 534px;
    height: 304px;
    border-radius: 18px;
    overflow: hidden;
    box-shadow: 0 4px 12px rgba(0,0,0,0.18);
  }
  .card--front { left: 48px; top: 60px; background: var(--card-white); }
  .card--back { left: 612px; top: 66px; background: var(--brand-blue); }

  .card__wave { position: absolute; left: 0; top: 0; }

  .brand-name {
    position: absolute;
    font-weight: 800;
    color: var(--brand-blue);
    white-space: nowrap;
    letter-spacing: 0.5px;
  }
  .brand-tagline {
    position: absolute;
    color: var(--brand-blue);
    font-size: 15.5px;
    letter-spacing: 3.4px;
    white-space: nowrap;
  }
  .card--front .brand-name { left: 46px; top: 24px; font-size: 37px; }
  .card--front .brand-tagline { left: 47px; top: 80px; }

  .holder-name {
    position: absolute;
    left: 46px; top: 160px;
    font-size: 20px;
    font-weight: 700;
    font-style: italic;
    color: var(--ink-dark);
    text-transform: uppercase;
    white-space: nowrap;
  }
  .contact-divider {
    position: absolute;
    left: 272px; top: 128px;
    width: 1px; height: 92px;
    background: var(--rule-grey);
  }
  .contact-list {
    position: absolute;
    left: 288px; top: 140px;
    list-style: none;
    font-size: 13.5px;
    line-height: 18.5px;
    color: var(--ink-body);
  }
  .contact-list li { white-space: nowrap; display: flex; align-items: center; gap: 6px; }
  .contact-list svg { flex: none; }
  .card__web {
    position: absolute;
    right: 28px; bottom: 14px;
    font-size: 13.5px;
    color: var(--card-white);
  }

  .back-band {
    position: absolute;
    left: 0; top: 128px;
    width: 100%; height: 86px;
    background: var(--card-white);
  }
  .card--back .brand-name { left: 56px; top: 6px; font-size: 34px; }
  .card--back .brand-tagline { left: 58px; top: 56px; font-size: 14.5px; letter-spacing: 3.2px; }
</style>
</head>
<body>
  <section class="card card--front" aria-label="Business card front">
    <svg class="card__wave" width="534" height="304" viewBox="0 0 534 304" aria-hidden="true">
      <path d="M0,196 C110,240 230,262 360,258" fill="none" stroke="var(--swoosh-grey)" stroke-width="3"/>
      <path d="M0,210 C150,266 340,272 534,200 L534,304 L0,304 Z" fill="var(--brand-blue)"/>
    </svg>
    <div class="brand-name">RIDGETOP GEARWORKS</div>
    <div class="brand-tagline">THE KIT•THE CLIMB•THE OUTDOORS</div>

    <div class="holder-name">Gordon Pellimore</div>
    <div class="contact-divider"></div>
    <ul class="contact-list">
      <li>Unit 3, 14-16 Marlowe Street</li>
      <li>Kellerby Bay, TAS, 2371</li>
      <li>
        <svg width="11" height="12" viewBox="0 0 11 12" aria-hidden="true"><path d="M2,1 L4,1 L5,4 L3.5,5 C4.2,7 5.5,8.3 7,9 L8,7.5 L10.5,8.5 L10.5,10.5 C6,11.5 0.5,6 1,1.5 Z" fill="var(--ink-body)"/></svg>
        0438 627 194
      </li>
      <li>
        <svg width="12" height="10" viewBox="0 0 12 10" aria-hidden="true"><rect x="0.7" y="1.2" width="10.6" height="7.6" fill="none" stroke="var(--ink-body)" stroke-width="1.2"/><path d="M0.7,1.2 L6,5.5 L11.3,1.2" fill="none" stroke="var(--ink-body)" stroke-width="1.2"/></svg>
        mark@ridgetopgearworks.com
      </li>
    </ul>
    <div class="card__web">www.ridgetopgearworks.com.au</div>
  </section>

  <section class="card card--back" aria-label="Business card back">
    <div class="back-band">
      <div class="brand-name">RIDGETOP GEARWORKS</div>
      <div class="brand-tagline">THE KIT•THE CLIMB•THE OUTDOORS</div>
    </div>
  </section>
</body>
</html>
```